Pavecrest Works

Im looking for something similar to (tarvalepaving.com) web site. I really want it to pop!
services we offer:
- Seal Coating
- Crack Filling
- Striping
- Asphalt
- Concrete
- Signage
- Road Grinding
- Grading
- Hydro Blasting
- Recycled asphalt
- Dumpster Pads
- Pressure Washing
- Wheel blocks
- Bollard installation
- Commercial Curbing
- Job site clean up
- Sweeping
- Forestry Clean up
- ADA Compliant work
- Speed bump installation and removal
- Snow removal
- Custom stair sets (Commercial)
Target Market(s)
Parking lot maintenance, asphalt repairs, road grading
Industry/Entity Type
construction, parking lot maintenance
Number of Pages Required
2 page

```html
<!DOCTYPE html>
<html lang="en">
<head>
<meta charset="utf-8">
<title>Pavecrest Works</title>
<link href="https://fonts.googleapis.com/css2?family=Montserrat:wght@500;600;700;800&family=Roboto:wght@400;500;700&display=swap" rel="stylesheet">
<style>
:root{
  --green:#76ff03;
  --black:#000;
  --white:#fff;
  --ink:#111;
  --grey-bg:#f3f3f3;
  --muted:#666;
  --line:#cfcfcf;
}
*{margin:0;padding:0;box-sizing:border-box}
html,body{width:1200px;height:4515px;overflow:hidden}
body{position:relative;background:var(--white);font-family:Roboto,Arial,sans-serif;color:var(--ink)}
.abs{position:absolute}
.head-font{font-family:Montserrat,Arial,sans-serif}

/* header */
.site-header{left:0;top:0;width:1200px;height:115px;background:var(--white)}
.brand{left:110px;top:22px;font-family:Montserrat,sans-serif;font-weight:800;color:var(--black);line-height:1}
.brand .b1{display:block;font-size:43px;letter-spacing:-1px}
.brand .b2{display:block;font-size:16px;letter-spacing:12px;margin-top:4px}
.main-nav{left:398px;top:66px;display:flex;gap:33px;font:700 13px Roboto,sans-serif}
.main-nav a{color:var(--ink);text-decoration:none}
.main-nav a.active{color:var(--green);border-bottom:2px solid var(--green);padding-bottom:5px}
.top-social{left:625px;top:19px;display:flex;gap:10px}
.top-social span{width:30px;height:30px;border:2px solid var(--green);border-radius:50%}
.call-line{left:829px;top:27px;font:700 13px Roboto,sans-serif}
.call-btn{left:868px;top:55px;width:182px;height:36px;border:3px solid var(--green);font:700 13px Roboto,sans-serif;display:flex;align-items:center;justify-content:center;gap:6px}

/* hero */
.hero-photo{left:0;top:115px;width:1200px;height:690px;background:linear-gradient(180deg,#8ea0b4 0%,#a9b3ba 22%,#8b8a80 36%,#4a4a48 55%,#3a3a3a 100%)}
.hero-title{left:0;top:332px;width:1200px;text-align:center;font:800 52px/1.05 Montserrat,sans-serif;color:var(--white)}
.hero-btn{left:534px;top:464px;width:132px;height:39px;border:3px solid var(--green);color:var(--green);font:700 12px Roboto,sans-serif;display:flex;align-items:center;justify-content:center}
.slide-arrow{top:436px;width:44px;height:44px;border-radius:50%;background:rgba(0,0,0,.55);color:var(--white);display:flex;align-items:center;justify-content:center}
.dots{left:571px;top:755px;display:flex;gap:8px;align-items:center}
.dots span{width:12px;height:12px;border-radius:50%;background:var(--white)}
.dots span.on{width:18px;height:18px;background:var(--green)}

/* bands */
.bands{left:0;top:0}

/* about */
.hex-frame{left:131px;top:955px;width:396px;height:446px;background:var(--green);clip-path:polygon(50% 0,100% 25%,100% 75%,50% 100%,0 75%,0 25%)}
.hex-photo{left:131px;top:955px;width:391px;height:430px;clip-path:polygon(50% 0,100% 25%,100% 75%,50% 100%,0 75%,0 25%);background:linear-gradient(180deg,#9aa9b6 0%,#b6a06a 30%,#8c6a3e 60%,#5c4a36 100%)}
.play{left:295px;top:1144px;width:64px;height:64px;border-radius:50%;background:var(--green);display:flex;align-items:center;justify-content:center}
.ghost{font-family:Montserrat,sans-serif;font-weight:800;white-space:nowrap}
.ghost-dark{color:#141414}
.ghost-light{color:#ececec}
.section-title{font:800 34px Montserrat,sans-serif;white-space:nowrap}
.about-title{left:617px;top:990px;color:var(--white)}
.about-text{left:617px;top:1047px;width:472px;color:var(--white);font:400 13.6px/22.2px Roboto,sans-serif}
.outline-btn{border:3px solid var(--green);display:flex;align-items:center;justify-content:center;font:700 13px Roboto,sans-serif}
.about-btn{left:617px;top:1317px;width:133px;height:43px;color:var(--green)}

/* services */
.services-title{left:0;top:1583px;width:1200px;text-align:center}
.service-card{width:312px;height:253px;background:var(--black);color:var(--white);text-align:center}
.service-card h3{position:absolute;left:0;top:93px;width:100%;font:700 20px Roboto,sans-serif}
.service-card p{position:absolute;left:28px;top:136px;width:256px;font:400 13.4px/21.6px Roboto,sans-serif}
.diamond{width:110px;height:110px;transform:rotate(45deg);background:var(--green);border:4px solid var(--green);box-shadow:inset 0 0 0 3px var(--black)}
.diamond-icon{width:154px;height:154px;display:flex;align-items:center;justify-content:center}
.more-btn{left:504px;top:2365px;width:192px;height:46px;color:var(--ink)}

/* blog */
.blog-bg{left:0;top:2400px;width:1200px;height:820px;background:linear-gradient(180deg,#262626 0%,#1b1b1b 45%,#222 100%)}
.blog-title{left:0;top:2635px;width:1200px;text-align:center;color:var(--white)}
.blog-photo{top:2721px;width:311px;height:200px}
.blog-date{top:2945px;color:var(--green);font:500 15px Montserrat,sans-serif;letter-spacing:4px}
.blog-head{top:2975px;color:var(--white);font:700 18px Roboto,sans-serif}
.blog-text{top:3008px;width:318px;color:#ddd;font:400 13.6px/26px Roboto,sans-serif}
.blog-more{top:3096px;color:var(--green);font:700 13px Roboto,sans-serif;text-decoration:underline}

/* contact */
.contact-title{left:0;top:3312px;width:1200px;text-align:center}
.info{width:280px;text-align:center}
.info .ring{width:62px;height:62px;margin:0 auto;border:2px solid var(--green);border-radius:50%;display:flex;align-items:center;justify-content:center}
.info h4{margin-top:12px;font:500 13.6px Montserrat,sans-serif}
.info p{margin-top:4px;font:400 12.6px/20px Roboto,sans-serif;color:#333}
.field{border:1px solid var(--line);background:var(--white);color:#888;font:400 13px Roboto,sans-serif;padding:0 21px;display:flex;align-items:center}
.field.msg{align-items:flex-start;padding-top:24px}
.submit{left:519px;top:3860px;width:162px;height:52px;border-radius:26px;color:var(--ink);font-size:15px}

/* footer */
.subscribe{left:373px;top:4117px;width:452px;height:41px;background:var(--white);border-radius:21px;overflow:hidden;display:flex;align-items:center}
.subscribe span{padding-left:35px;flex:1;color:#888;font:400 13px Roboto,sans-serif}
.subscribe b{width:150px;height:41px;background:var(--green);border-radius:21px;display:flex;align-items:center;justify-content:center;font:700 13px Roboto,sans-serif}
.foot-h{top:4217px;color:var(--white);font:700 22px Roboto,sans-serif}
.foot-list{color:var(--white);font:400 14.5px/28px Roboto,sans-serif;list-style:none}
.foot-list li{display:flex;align-items:flex-start;gap:14px}
.foot-list svg{flex:none;margin-top:9px}
.divider{top:4222px;width:1px;height:176px;background:#cfcfcf}
.foot-social{left:898px;top:4266px;display:flex;gap:9px}
.foot-social span{width:37px;height:37px;border:2px solid var(--white);border-radius:50%}
.copyright{left:0;top:4446px;width:1200px;text-align:center;color:var(--white);font:400 13.5px Roboto,sans-serif}
</style>
</head>
<body>

<header class="site-header abs">
  <div class="brand abs"><span class="b1">PAVECREST</span><span class="b2">WORKS</span></div>
  <nav class="main-nav abs">
    <a class="active" href="#">HOME</a><a href="#">ABOUT</a><a href="#">SERVICES</a><a href="#">BLOG</a><a href="#">CONTACT</a>
  </nav>
  <div class="top-social abs" aria-label="Social links"><span></span><span></span><span></span><span></span></div>
  <div class="call-line abs">CALL US TODAY FOR A FREE ESTIMATE</div>
  <div class="call-btn abs">
    <svg width="12" height="12" viewBox="0 0 24 24"><path d="M6.6 10.8c1.4 2.8 3.8 5.1 6.6 6.6l2.2-2.2c.3-.3.7-.4 1-.2 1.1.4 2.3.6 3.6.6.6 0 1 .4 1 1V20c0 .6-.4 1-1 1C10.6 21 3 13.4 3 4c0-.6.4-1 1-1h3.5c.6 0 1 .4 1 1 0 1.3.2 2.5.6 3.6.1.3 0 .7-.2 1z" fill="#111"/></svg>
    +1 888 888 8888
  </div>
</header>

<div class="hero-photo abs" role="img" aria-label="Photo of a yellow road roller on fresh asphalt in a parking lot"></div>
<div class="blog-bg abs" role="img" aria-label="Dark photo of a compact track loader on a job site"></div>

<svg class="bands abs" width="1200" height="4515" viewBox="0 0 1200 4515" aria-hidden="true">
  <polygon points="0,762 600,800 1200,762 1200,1590 600,1462 0,1590" fill="#000"/>
  <polyline points="0,760 600,798 1200,760" fill="none" stroke="#76ff03" stroke-width="9"/>
  <polygon points="0,1585 600,1459 1200,1585 1200,2418 600,2540 0,2418" fill="#fff"/>
  <polyline points="0,1587 600,1461 1200,1587" fill="none" stroke="#76ff03" stroke-width="9"/>
  <polyline points="0,2420 600,2542 1200,2420" fill="none" stroke="#76ff03" stroke-width="9"/>
  <polygon points="0,3211 1200,3211 1200,4082 600,3991 0,4082" fill="#f3f3f3"/>
  <polygon points="0,4082 600,3991 1200,4082 1200,4515 0,4515" fill="#000"/>
  <polyline points="0,4082 600,3991 1200,4082" fill="none" stroke="#76ff03" stroke-width="9"/>
</svg>

<!-- hero -->
<h1 class="hero-title abs">PAVECREST<br>WORKS</h1>
<div class="hero-btn abs">GET STARTED</div>
<div class="slide-arrow abs" style="left:35px"><svg width="10" height="14" viewBox="0 0 10 14"><path d="M7 2 2 7l5 5" fill="none" stroke="#fff" stroke-width="2"/></svg></div>
<div class="slide-arrow abs" style="left:1120px"><svg width="10" height="14" viewBox="0 0 10 14"><path d="m3 2 5 5-5 5" fill="none" stroke="#fff" stroke-width="2"/></svg></div>
<div class="dots abs"><span></span><span class="on"></span><span></span></div>

<!-- about -->
<div class="hex-frame abs"></div>
<div class="hex-photo abs" role="img" aria-label="Photo of a compact track loader grading soil beside a cornfield"></div>
<div class="play abs"><svg width="22" height="24" viewBox="0 0 22 24"><path d="M3 2 20 12 3 22z" fill="#000"/></svg></div>
<div class="ghost ghost-dark abs" style="left:475px;top:950px;font-size:76px">WHO WE ARE</div>
<h2 class="section-title about-title abs">ABOUT US</h2>
<p class="about-text abs">Lorem ipsum dolor sit amet, consectetur adipiscing elit, sed do eiusmod tempor incididunt ut labore et dolore magna aliqua. Ut enim ad minim veniam, quis nostrud exercitation ullamco laboris nisi ut aliquip ex ea commodo consequat. Duis aute irure dolor in reprehenderit in voluptate velit esse cillum dolore eu fugiat nulla pariatur. Excepteur sint occaecat cupidatat non proident, sunt in culpa qui officia deserunt mollit anim id est laborum.Lorem ipsum dolor sit amet, consectetur adipiscing elit, sed do eiusmod tempor incididunt ut labore et dolore magna aliqua. Ut enim ad minim veniam, quis nostrud exercitation ullamco laboris nisi ut aliquip ex ea commodo consequat. Duis aute irure dolor in reprehenderit in voluptate velit esse cillum dolore eu fugiat nulla pariatur.</p>
<div class="outline-btn about-btn abs">LEARN MORE</div>

<!-- services -->
<div class="ghost ghost-light abs" style="left:0;top:1555px;width:1200px;text-align:center;font-size:84px">WE OFFERED</div>
<h2 class="section-title services-title abs">OUR SERVICES</h2>

<div class="service-card abs" style="left:110px;top:1738px"><h3>Seal Coating</h3><p>Lorem ipsum dolor sit amet, consectetur adipiscing elit, sed do eiusmod tempor incididunt ut labore et dolore magna aliqua. Ut enim ad minim</p></div>
<div class="service-card abs" style="left:443px;top:1738px"><h3>Crack Filling</h3><p>Lorem ipsum dolor sit amet, consectetur adipiscing elit, sed do eiusmod tempor incididunt ut labore et dolore magna aliqua. Ut enim ad minim</p></div>
<div class="service-card abs" style="left:776px;top:1738px"><h3>Striping</h3><p>Lorem ipsum dolor sit amet, consectetur adipiscing elit, sed do eiusmod tempor incididunt ut labore et dolore magna aliqua. Ut enim ad minim</p></div>
<div class="service-card abs" style="left:110px;top:2088px"><h3>Asphalt</h3><p>Lorem ipsum dolor sit amet, consectetur adipiscing elit, sed do eiusmod tempor incididunt ut labore et dolore magna aliqua. Ut enim ad minim</p></div>
<div class="service-card abs" style="left:443px;top:2088px"><h3>Concrete</h3><p>Lorem ipsum dolor sit amet, consectetur adipiscing elit, sed do eiusmod tempor incididunt ut labore et dolore magna aliqua. Ut enim ad minim</p></div>
<div class="service-card abs" style="left:776px;top:2088px"><h3>Signage</h3><p>Lorem ipsum dolor sit amet, consectetur adipiscing elit, sed do eiusmod tempor incididunt ut labore et dolore magna aliqua. Ut enim ad minim</p></div>

<div class="diamond abs" style="left:211px;top:1683px"></div>
<div class="diamond abs" style="left:544px;top:1683px"></div>
<div class="diamond abs" style="left:877px;top:1683px"></div>
<div class="diamond abs" style="left:211px;top:2033px"></div>
<div class="diamond abs" style="left:544px;top:2033px"></div>
<div class="diamond abs" style="left:877px;top:2033px"></div>

<div class="diamond-icon abs" style="left:189px;top:1661px"><svg width="56" height="50" viewBox="0 0 56 50"><circle cx="18" cy="7" r="6" fill="#000"/><path d="M12 16h10l6 14-6 2-4-8-4 10 5 14h-6l-6-16z" fill="#000"/><path d="M30 48 44 26l12 22z" fill="#000"/><rect x="0" y="46" width="56" height="4" fill="#000"/></svg></div>
<div class="diamond-icon abs" style="left:522px;top:1661px"><svg width="50" height="50" viewBox="0 0 50 50"><rect x="12" y="2" width="26" height="28" fill="#000"/><rect x="17" y="8" width="5" height="6" fill="#76ff03"/><rect x="28" y="8" width="5" height="6" fill="#76ff03"/><rect x="17" y="19" width="5" height="6" fill="#76ff03"/><rect x="2" y="34" width="46" height="14" fill="#000"/><rect x="6" y="39" width="38" height="3" fill="#76ff03"/></svg></div>
<div class="diamond-icon abs" style="left:855px;top:1661px"><svg width="54" height="50" viewBox="0 0 54 50"><path d="M27 2 46 44H8z" fill="#000"/><rect x="14" y="16" width="26" height="4" fill="#76ff03"/><rect x="10" y="30" width="34" height="4" fill="#76ff03"/><rect x="2" y="44" width="50" height="5" fill="#000"/></svg></div>
<div class="diamond-icon abs" style="left:189px;top:2011px"><svg width="60" height="44" viewBox="0 0 60 44"><rect x="6" y="4" width="22" height="4" fill="#000"/><rect x="10" y="8" width="4" height="12" fill="#000"/><rect x="4" y="18" width="32" height="12" fill="#000"/><circle cx="12" cy="36" r="7" fill="#000"/><circle cx="48" cy="30" r="10" fill="#000"/><circle cx="48" cy="30" r="4" fill="#76ff03"/><rect x="36" y="26" width="6" height="6" fill="#000"/></svg></div>
<div class="diamond-icon abs" style="left:522px;top:2011px"><svg width="48" height="50" viewBox="0 0 48 50"><rect x="2" y="2" width="44" height="46" fill="#000"/><rect x="9" y="7" width="5" height="36" fill="#76ff03"/><rect x="21" y="7" width="6" height="36" fill="#76ff03"/><rect x="34" y="7" width="5" height="36" fill="#76ff03"/></svg></div>
<div class="diamond-icon abs" style="left:855px;top:2011px"><svg width="50" height="54" viewBox="0 0 50 54"><rect x="22" y="0" width="6" height="54" fill="#000"/><path d="M6 8h34l8 7-8 7H6z" fill="#000"/><path d="M44 28H10l-8 7 8 7h34z" fill="#000"/></svg></div>

<div class="outline-btn more-btn abs">VIEW MORE SERVICES</div>

<!-- blog -->
<div class="ghost abs" style="left:0;top:2610px;width:1200px;text-align:center;font-size:80px;color:#2c2c2c">BLOG POST</div>
<h2 class="section-title blog-title abs">OUR LATEST BLOG</h2>

<div class="blog-photo abs" style="left:111px;background:linear-gradient(160deg,#6f8a58,#8a7358 50%,#b59b4a)" role="img" aria-label="Photo of a track loader clearing a dirt trail in a forest"></div>
<div class="blog-photo abs" style="left:444px;background:linear-gradient(170deg,#8aa2b8,#8f8a7a 40%,#6e6253)" role="img" aria-label="Photo of a loader grading gravel on a lot"></div>
<div class="blog-photo abs" style="left:777px;background:linear-gradient(160deg,#8a9c88,#b0aca4 45%,#d9c35a 70%,#9c9a94)" role="img" aria-label="Photo of new concrete ramp with a yellow tactile pad"></div>

<div class="blog-date abs" style="left:110px">📅 JANUARY 30,2020</div>
<div class="blog-date abs" style="left:442px">📅 JANUARY 30,2020</div>
<div class="blog-date abs" style="left:775px">📅JANUARY 30,2020</div>
<h3 class="blog-head abs" style="left:109px">LOREM IPSUM DOLOR SIT AMET</h3>
<h3 class="blog-head abs" style="left:442px">LOREM IPSUM DOLOR SIT AMET</h3>
<h3 class="blog-head abs" style="left:775px">LOREM IPSUM DOLOR SIT AMET</h3>
<p class="blog-text abs" style="left:109px">Lorem ipsum dolor sit amet, consectetur adipi scing elit, sed do eiusmod tempor incididunt ut labore et dolore magna aliqua.</p>
<p class="blog-text abs" style="left:442px">Lorem ipsum dolor sit amet, consectetur adipi scing elit, sed do eiusmod tempor incididunt ut labore et dolore magna aliqua.</p>
<p class="blog-text abs" style="left:775px">Lorem ipsum dolor sit amet, consectetur adipi scing elit, sed do eiusmod tempor incididunt ut labore et dolore magna aliqua.</p>
<a class="blog-more abs" style="left:109px">CONTINUE READING ➔</a>
<a class="blog-more abs" style="left:442px">CONTINUE READING ➔</a>
<a class="blog-more abs" style="left:775px">CONTINUE READING ➔</a>

<!-- contact -->
<div class="ghost ghost-light abs" style="left:0;top:3280px;width:1200px;text-align:center;font-size:80px">GET IN TOUCH</div>
<h2 class="section-title contact-title abs">CONTACT US</h2>

<div class="info abs" style="left:228px;top:3392px">
  <div class="ring"><svg width="18" height="24" viewBox="0 0 18 24"><path d="M9 0a9 9 0 0 0-9 9c0 7 9 15 9 15s9-8 9-15a9 9 0 0 0-9-9z" fill="#111"/><circle cx="9" cy="9" r="3.5" fill="#f3f3f3"/></svg></div>
  <h4>ADDRESS :</h4>
  <p>Address: 2480 Cedar Ridge Rd<br>#12, Fairhaven, OR 97402</p>
</div>
<div class="info abs" style="left:466px;top:3392px">
  <div class="ring"><svg width="20" height="20" viewBox="0 0 24 24"><path d="M6.6 10.8c1.4 2.8 3.8 5.1 6.6 6.6l2.2-2.2c.3-.3.7-.4 1-.2 1.1.4 2.3.6 3.6.6.6 0 1 .4 1 1V20c0 .6-.4 1-1 1C10.6 21 3 13.4 3 4c0-.6.4-1 1-1h3.5c.6 0 1 .4 1 1 0 1.3.2 2.5.6 3.6.1.3 0 .7-.2 1z" fill="#111"/></svg></div>
  <h4>PHONE :</h4>
  <p>+1 888 888 8888</p>
</div>
<div class="info abs" style="left:706px;top:3392px">
  <div class="ring"><svg width="24" height="18" viewBox="0 0 24 18"><rect width="24" height="18" rx="2" fill="#111"/><path d="m2 3 10 7 10-7" fill="none" stroke="#f3f3f3" stroke-width="2"/></svg></div>
  <h4>EMAIL :</h4>
  <p>info@companyname.com</p>
</div>

<div class="field abs" style="left:238px;top:3553px;width:351px;height:57px">First name</div>
<div class="field abs" style="left:608px;top:3553px;width:351px;height:57px">Last name</div>
<div class="field abs" style="left:238px;top:3628px;width:351px;height:57px">Phone</div>
<div class="field abs" style="left:608px;top:3628px;width:351px;height:57px">Email address</div>
<div class="field msg abs" style="left:238px;top:3705px;width:721px;height:135px">Message</div>
<div class="outline-btn submit abs">SUBMIT</div>

<!-- footer -->
<div class="subscribe abs"><span>Email address</span><b>SUBSCRIBE</b></div>

<h3 class="foot-h abs" style="left:138px">Links</h3>
<ul class="foot-list abs" style="left:140px;top:4263px"><li>Home</li><li>Services</li><li>Blog</li><li>Contact</li></ul>
<div class="divider abs" style="left:336px"></div>

<h3 class="foot-h abs" style="left:461px">Contact us</h3>
<ul class="foot-list abs" style="left:461px;top:4263px;width:320px">
  <li><svg width="10" height="13" viewBox="0 0 18 24"><path d="M9 0a9 9 0 0 0-9 9c0 7 9 15 9 15s9-8 9-15a9 9 0 0 0-9-9z" fill="#fff"/></svg><span>123,Lorem ipsum dolor sit amet,<br>consec</span></li>
  <li><svg width="12" height="12" viewBox="0 0 24 24"><path d="M6.6 10.8c1.4 2.8 3.8 5.1 6.6 6.6l2.2-2.2c.3-.3.7-.4 1-.2 1.1.4 2.3.6 3.6.6.6 0 1 .4 1 1V20c0 .6-.4 1-1 1C10.6 21 3 13.4 3 4c0-.6.4-1 1-1h3.5c.6 0 1 .4 1 1 0 1.3.2 2.5.6 3.6.1.3 0 .7-.2 1z" fill="#fff"/></svg><span>+1 888 888 8888</span></li>
  <li><svg width="13" height="10" viewBox="0 0 24 18"><rect width="24" height="18" rx="2" fill="#fff"/><path d="m2 3 10 7 10-7" fill="none" stroke="#000" stroke-width="2"/></svg><span>info@companyname.com</span></li>
</ul>
<div class="divider abs" style="left:818px"></div>

<h3 class="foot-h abs" style="left:944px">Follow us</h3>
<div class="foot-social abs" aria-label="Social links"><span></span><span></span><span></span><span></span></div>

<p class="copyright abs">© Copyrights.2021.The Company Name.All Rights Reserved</p>

</body>
</html>
```